Stage Design Company Business Card

We are looking to step up up our business card design for our team.

We are a Full service Design and Consultation company for Stage and TV with an emphasis in Theatrical Lighting.

We like our materials to be clean and modern with solid colors free of patterns and gradients. Our brand consists of 4 primary colors Purple, Black, Grey, and White. Provided is our Word Mark as well as our Symbol Logo.

We would like our cards to leave an impression beyond the information, show our attention to design and detail, and make our marks an easily recognized feature (together or apart) for our clients.

We need a warm approachable comfortable feel for some clients, and a professional flair for the board member type clients.

Attached are our brand elements, and our existing cards to give a sense of our style and a glipse at the information we provide on our cards.

Target Market(s)

broad client base from church leaders to high school teachers and architects.

Industry/Entity Type

Business

Contact Information for Business Card

We format our phone number with periods not parenthesis or dashes. Information will be edited for each of our team members, and team member specific cards are not part of this scope, but rather a template so to speak.

Font styles to use
Sans Serif

Colors
6b449b
ffffff
000000
333333
aaaaaa

Requirements
Must have
• Wordmark and logo mark present (does not need to exist on the same side of card)
• Brand Colors,
• Name, Phone, Email, Address.
• Unique choices that make someone stop and take a second look
Nice to have
• It would be nice to somehow convey what we DO, as our brand name does not lend itself to this, outside of an obvious tagline though.....
• social media if not crowded. all of our handles match (instagram, twitter, facebook)
Should not have
• "clipart"

```html
<!DOCTYPE html>
<html lang="en">
<head>
<meta charset="utf-8">
<title>Stage Design Company Business Card</title>
<link href="https://fonts.googleapis.com/css2?family=Source+Sans+3:ital,wght@0,400;0,600;1,600&display=swap" rel="stylesheet">
<style>
  :root {
    --purple: #36226c;
    --white: #ffffff;
    --canvas: #ecebef;
  }
  * { box-sizing: border-box; margin: 0; padding: 0; }
  html, body {
    width: 1200px;
    height: 899px;
    overflow: hidden;
    background: var(--canvas);
    font-family: "Source Sans 3", "Myriad Pro", Arial, sans-serif;
  }
  .card {
    position: absolute;
    width: 556px;
    height: 342px;
    box-shadow: 0 6px 18px rgba(0,0,0,0.18);
    overflow: hidden;
  }
  .card-front { left: 239px; top: 61px; background: var(--purple); color: var(--white); }
  .card-back  { left: 457px; top: 518px; background: var(--white); }

  .front-panel { position: absolute; right: 0; top: 0; width: 240px; height: 342px; }

  .identity { position: absolute; left: 37px; top: 78px; }
  .person-name { font-size: 23px; font-weight: 400; line-height: 1.1; }
  .person-title { font-size: 15px; line-height: 1.3; }
  .address { margin-top: 20px; font-size: 15px; line-height: 1.35; }
  .contacts { margin-top: 14px; list-style: none; font-size: 15px; line-height: 1.35; }
  .contacts li { display: flex; align-items: center; gap: 8px; }
  .contacts svg { width: 11px; height: 11px; fill: var(--white); flex: none; }

  .brand {
    position: absolute;
    left: 0; right: 0; top: 128px;
    display: flex; justify-content: center; align-items: center; gap: 26px;
    color: var(--purple);
  }
  .brand-dot { width: 62px; height: 62px; border-radius: 50%; border: 5px solid var(--purple); }
  .brand-name { font-size: 34px; font-weight: 600; letter-spacing: 22px; }

  .tagline-band {
    position: absolute;
    left: 0; right: 0; top: 268px; height: 54px;
    background: var(--purple);
    color: var(--white);
    display: flex; flex-direction: column; justify-content: center; align-items: center;
    font-size: 16px; font-weight: 600; font-style: italic; line-height: 1.3;
    text-align: center;
  }
</style>
</head>
<body>
  <section class="card card-front">
    <svg class="front-panel" viewBox="0 0 240 342" aria-hidden="true">
      <path d="M70 0 H240 V342 H40 C10 300 20 250 40 220 C70 180 60 120 55 80 C52 40 58 15 70 0 Z" fill="#ffffff"/>
      <circle cx="150" cy="180" r="70" fill="none" stroke="#36226c" stroke-width="8"/>
    </svg>
    <div class="identity">
      <h1 class="person-name">Marcus Ellery</h1>
      <p class="person-title">Managing Director</p>
      <p class="address">480 Fenwick Lane<br>Harbor City, 204518.</p>
      <ul class="contacts">
        <li><svg viewBox="0 0 24 24"><path d="M6.6 10.8a15 15 0 0 0 6.6 6.6l2.2-2.2a1 1 0 0 1 1-.25 11.4 11.4 0 0 0 3.6.57 1 1 0 0 1 1 1V20a1 1 0 0 1-1 1A17 17 0 0 1 3 4a1 1 0 0 1 1-1h3.5a1 1 0 0 1 1 1c0 1.25.2 2.45.57 3.57a1 1 0 0 1-.25 1z"/></svg>312.555.0148</li>
        <li><svg viewBox="0 0 24 24"><path d="M2 5h20v14H2z M2 5l10 8 10-8" fill="#ffffff"/><path d="M3 6l9 7 9-7" fill="none" stroke="#36226c" stroke-width="2"/></svg>hello@novarstage.com</li>
        <li><svg viewBox="0 0 24 24"><path d="M10 14a4 4 0 0 1 0-5.6l3-3a4 4 0 0 1 5.6 5.6l-1.5 1.5-1.4-1.4 1.5-1.5a2 2 0 0 0-2.8-2.8l-3 3a2 2 0 0 0 0 2.8zm4-4a4 4 0 0 1 0 5.6l-3 3a4 4 0 0 1-5.6-5.6l1.5-1.5 1.4 1.4-1.5 1.5a2 2 0 0 0 2.8 2.8l3-3a2 2 0 0 0 0-2.8z"/></svg>www.novarstage.com</li>
      </ul>
    </div>
  </section>

  <section class="card card-back">
    <div class="brand">
      <span class="brand-dot" aria-hidden="true"></span>
      <span class="brand-name">NOVAR</span>
    </div>
    <div class="tagline-band">
      <p>Design and Consultation company for</p>
      <p>Stage and TV with an emphasis in Theatrical Lighting.</p>
    </div>
  </section>
</body>
</html>
```